English and Spanish Language School Needs a Business Card

Need a business card design a startup company called Maribel Language School. The company will offer English and Spanish conversational level courses designed to make the learner feel comfortable with grammar and vocabulary. We would like to see a logo with some colour that should communicate learning, growth.

Target Market(s)

Consumers and businesses

Industry/Entity Type

Education

Contact Information for Business Card

TBD

Font styles to use
Serif

Requirements
Must have
• Include the following
• Logo
• Name
• Title
• Cellphone Number
• Office Phone number
• Email address
• Office Address

```html
<!DOCTYPE html>
<html lang="en">
<head>
<meta charset="utf-8">
<title>Maribel Language School — Business Card</title>
<link rel="stylesheet" href="https://fonts.googleapis.com/css2?family=Tinos:wght@400;700&display=swap">
<style>
  :root {
    --backdrop: #e9e6e1;
    --paper: #f7f7f7;
    --brand-red: #d42536;
    --brand-red-deep: #c21f30;
    --accent-teal: #1bb3b8;
    --ink-light: #fdfdfd;
  }
  * { box-sizing: border-box; margin: 0; padding: 0; }
  html, body {
    width: 1200px; height: 780px; overflow: hidden;
    background: var(--backdrop);
    font-family: "Tinos", "Times New Roman", serif;
  }
  .stage {
    position: relative; width: 1200px; height: 780px;
    display: flex; align-items: center; justify-content: center; gap: 24px;
  }
  .card {
    position: relative; width: 560px; height: 320px;
    background: var(--paper);
    box-shadow: 0 6px 18px rgba(0,0,0,0.18);
    overflow: hidden;
  }

  /* front */
  .card-front .red-band {
    position: absolute; left: 0; right: 0; top: 158px; height: 112px;
    background: linear-gradient(180deg, var(--brand-red), var(--brand-red-deep));
    border-top: 3px solid var(--paper);
    border-bottom: 3px solid var(--paper);
    box-shadow: 0 -3px 0 var(--accent-teal), 0 3px 0 var(--accent-teal);
  }
  .brand {
    position: absolute; display: flex; align-items: center; gap: 12px;
    color: var(--brand-red); font-weight: 700;
  }
  .brand-mark {
    width: 20px; height: 20px; border-radius: 50%;
    background: var(--accent-teal); flex: none;
  }
  .brand-name { line-height: 1; }
  .brand-name .main { display: block; }
  .brand-name .sub { display: block; }
  .card-front .brand { left: 34px; top: 44px; }
  .card-front .brand .main { font-size: 62px; }
  .card-front .brand .sub { font-size: 23px; margin-top: 4px; }

  .holder {
    position: absolute; right: 30px; top: 22px; text-align: right;
  }
  .holder-name { color: var(--brand-red); font-size: 15px; letter-spacing: 1px; }
  .holder-title { color: var(--accent-teal); font-size: 12px; }

  .contact-list {
    position: absolute; left: 30px; top: 196px; list-style: none;
    color: var(--ink-light); font-size: 15px;
  }
  .contact-list li { display: flex; align-items: center; gap: 8px; height: 22px; }
  .contact-list svg { width: 14px; height: 14px; flex: none; }
  .address {
    position: absolute; right: 30px; top: 186px; text-align: right;
    color: var(--ink-light); font-size: 15px; line-height: 1.5;
  }

  /* back */
  .card-back { background: linear-gradient(180deg, var(--brand-red), var(--brand-red-deep)); }
  .card-back .white-band {
    position: absolute; left: 0; right: 0; top: 78px; height: 164px;
    background: var(--paper);
    border-top: 3px solid var(--accent-teal);
    border-bottom: 3px solid var(--accent-teal);
    box-shadow: 0 -3px 0 var(--paper), 0 3px 0 var(--paper);
    display: flex; align-items: center; justify-content: center;
  }
  .card-back .brand { position: static; }
  .card-back .brand .main { font-size: 70px; }
  .card-back .brand .sub { font-size: 25px; margin-top: 4px; }
</style>
</head>
<body>
<main class="stage">
  <section class="card card-front" aria-label="Card front">
    <div class="brand">
      <span class="brand-mark"></span>
      <span class="brand-name"><span class="main">Maribel</span><span class="sub">Language School</span></span>
    </div>
    <div class="holder">
      <p class="holder-name">DANIEL REYES</p>
      <p class="holder-title">Maneger</p>
    </div>
    <div class="red-band"></div>
    <ul class="contact-list">
      <li>
        <svg viewBox="0 0 14 14" aria-hidden="true"><rect width="14" height="14" fill="#fff"/><rect x="4.5" y="2" width="5" height="10" rx="1" fill="none" stroke="#d42536" stroke-width="1.2"/></svg>
        555 014 2287
      </li>
      <li>
        <svg viewBox="0 0 14 14" aria-hidden="true"><rect width="14" height="14" fill="#fff"/><path d="M3 5 Q7 2 11 5 L10 7 L8.5 6 L5.5 6 L4 7 Z M4 8 H10 V11 H4 Z" fill="#d42536"/></svg>
        555 014 2290
      </li>
      <li>
        <svg viewBox="0 0 14 14" aria-hidden="true"><rect width="14" height="14" fill="#fff"/><rect x="2.5" y="4" width="9" height="6.5" fill="none" stroke="#d42536" stroke-width="1.2"/><path d="M2.5 4 L7 8 L11.5 4" fill="none" stroke="#d42536" stroke-width="1.2"/></svg>
        hello@maribelschool.com
      </li>
    </ul>
    <p class="address">48 Alder Lane, 2nd Ste<br>Brookfield, Texas 5678</p>
  </section>

  <section class="card card-back" aria-label="Card back">
    <div class="white-band">
      <div class="brand">
        <span class="brand-mark"></span>
        <span class="brand-name"><span class="main">Maribel</span><span class="sub">Language School</span></span>
      </div>
    </div>
  </section>
</main>
</body>
</html>
```